Brightfen Business Card Redesign & Logo Update

We need to update our business cards to something more modern and fresh. Brightfen can provide the current color schemes and old design examples, but welcome creativity in helping us with this redesign. PLEASE NOTE that we no longer utilize the "tree" and/or "leaf" imagery in our branding. If able would apprecaite an update on the quality of our "words only" logo in Ai. / PNG formats too.

Target Market(s)

Investors, landowners, corporate partners, contractors

Industry/Entity Type

Environmental Restoration & Conservation

Contact Information for Business Card

Logo, persons name, title, mailing address, phone and email, website url

Font styles to use
Other font styles liked:
• Merriweather

Requirements
Nice to have
• Logo, persons name, title, mailing address, phone and email, website url, but open to ideams
Should not have
• No all back backgrounds

```html
<!DOCTYPE html>
<html lang="en">
<head>
<meta charset="utf-8">
<title>Brightfen Business Card</title>
<link href="https://fonts.googleapis.com/css2?family=Oswald:wght@500;600&family=Arimo:wght@400&display=swap" rel="stylesheet">
<style>
  :root {
    --bg: #d9d9d9;
    --paper: #f7f7f7;
    --green: #0f6e33;
    --orange: #de7300;
    --ink: #1b1b1b;
    --grey-text: #7a7a7a;
    --white: #ffffff;
  }
  * { margin: 0; padding: 0; box-sizing: border-box; }
  html, body { width: 1200px; height: 793px; overflow: hidden; }
  body {
    background: var(--bg);
    display: flex;
    align-items: center;
    justify-content: center;
    gap: 50px;
  }
  .card {
    position: relative;
    width: 520px;
    height: 297px;
    border-radius: 16px;
    overflow: hidden;
    box-shadow: 0 6px 18px rgba(0,0,0,0.18);
  }
  .card--front { background: var(--paper); }
  .card--back {
    background: var(--green);
    display: flex;
    align-items: center;
    justify-content: center;
  }
  .card__swoosh { position: absolute; inset: 0; width: 100%; height: 100%; }

  .brand {
    position: absolute;
    left: 32px;
    top: 84px;
    font-family: "Oswald", sans-serif;
    text-transform: uppercase;
  }
  .brand__name {
    font-weight: 600;
    font-size: 42px;
    line-height: 1;
    letter-spacing: 1px;
    color: var(--green);
  }
  .brand__tagline {
    font-weight: 500;
    font-size: 11.5px;
    letter-spacing: 0.3px;
    color: var(--ink);
    line-height: 1.2;
  }
  .person {
    position: absolute;
    left: 32px;
    top: 186px;
  }
  .person__name {
    font-family: "Oswald", sans-serif;
    font-weight: 500;
    font-size: 22px;
    text-transform: uppercase;
    line-height: 1;
  }
  .person__first { color: var(--orange); }
  .person__last { color: var(--green); }
  .person__title {
    font-family: "Arimo", sans-serif;
    font-size: 11.5px;
    color: var(--grey-text);
    margin-top: 4px;
  }

  .contact {
    position: absolute;
    right: 24px;
    top: 60px;
    text-align: right;
    font-family: "Arimo", sans-serif;
    font-size: 12px;
    line-height: 1.45;
    color: var(--white);
    list-style: none;
  }
  .contact__gap { margin-top: 12px; }
  .contact__icon {
    width: 11px;
    height: 11px;
    margin-left: 5px;
    vertical-align: -1px;
    fill: none;
    stroke: var(--white);
    stroke-width: 1.6;
  }

  .back-brand {
    font-family: "Oswald", sans-serif;
    text-transform: uppercase;
    color: var(--white);
    text-align: center;
  }
  .back-brand__name {
    font-weight: 600;
    font-size: 88px;
    line-height: 0.95;
    letter-spacing: 2px;
  }
  .back-brand__tagline {
    font-weight: 500;
    font-size: 23px;
    letter-spacing: 0.5px;
    line-height: 1.1;
  }
</style>
</head>
<body>

  <section class="card card--front" aria-label="Business card front">
    <svg class="card__swoosh" viewBox="0 0 520 297" preserveAspectRatio="none" aria-hidden="true">
      <path d="M356 0 C 312 30, 300 120, 262 190 C 232 245, 176 282, 96 297 L520 297 L520 0 Z" fill="var(--green)"/>
      <path d="M372 0 C 328 32, 318 124, 280 194 C 250 248, 198 284, 124 297 L520 297 L520 0 Z" fill="var(--orange)"/>
    </svg>

    <div class="brand">
      <div class="brand__name">Brightfen</div>
      <div class="brand__tagline">Environmental Credit Company</div>
    </div>

    <div class="person">
      <div class="person__name"><span class="person__first">Daniel</span> <span class="person__last">Morrow</span></div>
      <div class="person__title">Managing Director</div>
    </div>

    <ul class="contact">
      <li>4120 Larch Hollow Road</li>
      <li>Fairbanks, Alaska 99701</li>
      <li>555-210-4837<svg class="contact__icon" viewBox="0 0 12 12"><path d="M2 1.5 L4.2 1.5 L5 4 L3.8 5 C4.5 6.6 5.4 7.5 7 8.2 L8 7 L10.5 7.8 L10.5 10 C6 10.5 1.5 6 2 1.5 Z"/></svg></li>
      <li>555-310-9265<svg class="contact__icon" viewBox="0 0 12 12"><rect x="3" y="1" width="6" height="10" rx="1"/></svg></li>
      <li>info@brightfen.com<svg class="contact__icon" viewBox="0 0 12 12"><rect x="1" y="2.5" width="10" height="7"/><path d="M1 2.5 L6 6.5 L11 2.5"/></svg></li>
      <li class="contact__gap">www.brightfen.com</li>
    </ul>
  </section>

  <section class="card card--back" aria-label="Business card back">
    <div class="back-brand">
      <div class="back-brand__name">Brightfen</div>
      <div class="back-brand__tagline">Environmental Credit Company</div>
    </div>
  </section>

</body>
</html>
```